Frostvale Harborline LLC

we need a business card design

Industry/Entity Type

hvac

Contact Information for Business Card

my logo

Requirements
Must have
• my logo and same colors

```html
<!DOCTYPE html>
<html lang="en">
<head>
<meta charset="utf-8">
<title>Frostvale Harborline LLC — Business Card</title>
<link rel="stylesheet" href="https://fonts.googleapis.com/css2?family=Lato:wght@400;700&family=Montserrat:wght@800&display=swap">
<style>
  :root {
    --bg: #e4e6e9;
    --paper: #ffffff;
    --brand-blue: #0d5ba3;
    --deep-blue: #123a6b;
    --gold: #f2b33d;
    --grey: #6d6f73;
    --ink-light: #ffffff;
  }
  * { box-sizing: border-box; margin: 0; padding: 0; }
  html, body { width: 1200px; height: 900px; overflow: hidden; }
  body {
    background: var(--bg);
    font-family: "Lato", sans-serif;
    display: flex;
    flex-direction: column;
    align-items: center;
    justify-content: center;
    gap: 40px;
  }
  .card {
    position: relative;
    width: 630px;
    height: 360px;
    background: var(--paper);
    box-shadow: 0 10px 28px rgba(0,0,0,0.18);
    overflow: hidden;
  }
  .card-front { display: flex; align-items: center; justify-content: center; }
  .brand {
    display: flex;
    align-items: center;
    gap: 12px;
  }
  .brand-dot {
    width: 22px; height: 22px;
    border-radius: 50%;
    background: var(--gold);
    flex: none;
  }
  .brand-name {
    font-family: "Montserrat", sans-serif;
    font-weight: 800;
    color: var(--brand-blue);
    text-transform: uppercase;
    line-height: 1.05;
  }
  .card-front .brand-name { font-size: 34px; }
  .card-back .brand {
    position: absolute;
    top: 40px; right: 44px;
  }
  .card-back .brand-dot { width: 16px; height: 16px; }
  .card-back .brand-name { font-size: 19px; }
  .wave { position: absolute; inset: 0; width: 100%; height: 100%; }
  .holder {
    position: absolute;
    left: 40px; top: 170px;
  }
  .holder-name {
    font-size: 22px;
    font-weight: 700;
    color: var(--deep-blue);
    letter-spacing: -0.5px;
  }
  .holder-role { font-size: 15px; color: var(--grey); margin-top: 2px; margin-left: 6px; }
  .contacts {
    position: absolute;
    left: 70px; top: 262px;
    list-style: none;
    color: var(--ink-light);
    font-size: 14px;
  }
  .contacts li { display: flex; align-items: center; gap: 10px; height: 25px; }
  .contacts svg { width: 15px; height: 15px; flex: none; }
  .address {
    position: absolute;
    left: 392px; top: 254px;
    padding-left: 18px;
    border-left: 1px solid var(--gold);
    color: var(--ink-light);
    font-size: 14px;
    line-height: 25px;
  }
</style>
</head>
<body>

  <section class="card card-front" aria-label="Card front">
    <div class="brand">
      <span class="brand-dot"></span>
      <span class="brand-name">Frostvale<br>Harborline LLC</span>
    </div>
  </section>

  <section class="card card-back" aria-label="Card back">
    <svg class="wave" viewBox="0 0 630 360" preserveAspectRatio="none" aria-hidden="true">
      <path d="M0,250 C170,205 360,110 556,112 L566,360 L0,360 Z" fill="var(--gold)"/>
      <path d="M0,260 C170,216 360,123 549,124 L557,360 L0,360 Z" fill="var(--brand-blue)"/>
    </svg>

    <div class="brand">
      <span class="brand-dot"></span>
      <span class="brand-name">Frostvale<br>Harborline LLC</span>
    </div>

    <div class="holder">
      <p class="holder-name">JOHN SMITH</p>
      <p class="holder-role">Director</p>
    </div>

    <ul class="contacts">
      <li>
        <svg viewBox="0 0 16 16" aria-hidden="true"><path d="M3.5 1.5l2.5 0 1 3.5-1.6 1.2c.8 1.7 2 2.9 3.6 3.7l1.2-1.6 3.5 1v2.5c0 .8-.7 1.4-1.5 1.4C6.6 13.2 2.8 9.4 2.1 3c0-.8.6-1.5 1.4-1.5z" fill="var(--gold)"/></svg>
        555-201-9000
      </li>
      <li>
        <svg viewBox="0 0 16 16" aria-hidden="true"><rect x="1.5" y="3.5" width="13" height="9" fill="none" stroke="var(--gold)" stroke-width="1.6"/><path d="M1.5 3.5l6.5 5 6.5-5" fill="none" stroke="var(--gold)" stroke-width="1.6"/></svg>
        info@frostvaleharborline.com
      </li>
      <li>
        <svg viewBox="0 0 16 16" aria-hidden="true"><g fill="none" stroke="var(--gold)" stroke-width="1.3"><circle cx="8" cy="8" r="6.5"/><ellipse cx="8" cy="8" rx="3" ry="6.5"/><path d="M1.5 8h13M2.5 4.8h11M2.5 11.2h11"/></g></svg>
        www.frostvaleharborline.com
      </li>
    </ul>

    <address class="address" style="font-style:normal">
      00 dummy city<br>
      dummy place 0000
    </address>
  </section>

</body>
</html>
```